Roofing web site brvt roofing

Look at some of our competitors web page we like something similar with NYC roofing
https://www.quillbarroofing.example/
Maybe a skyline picture of nyc at the home page with a picture of flat roofing installation

Target Market(s)

Commercial and residential flat roofs

Industry/Entity Type

Flat Roofing industry

Coding

Coded - Design and coding required

Number of Pages Required

2 page

Font styles to use
Decorative
Script

Colors

Designer to choose colors to be used in the design.

Requirements
Must have
• At BRVT Roofing, we are a trusted and reputable roofing company specializing in new construction flat roof installation and repair. With years of experience in the industry, we take pride in providing exceptional roofing solutions to our valued clients. Our team of highly skilled and dedicated roofing professionals understands the unique challenges and requirements of new construction projects. We work closely with builders, contractors, and architects to design and install flat roofs that meet the specific needs of each project. From commercial buildings to residential complexes, we have the expertise to deliver reliable and durable roofing solutions. When it comes to flat roof repairs, we are your go-to experts. Our experienced technicians conduct thorough inspections to identify the root cause of any issues your roof may be experiencing. We utilize the latest industry techniques and high-quality materials to efficiently repair your flat roof, ensuring its integrity and longevity. At BRVT Roofing, we prioritize customer satisfaction above all else. We believe in building strong relationships with our clients by providing exceptional craftsmanship and outstanding customer service. Our team is dedicated to delivering projects on time, within budget, and to the highest standards of quality. We understand that a well-maintained roof is essential for protecting your property and ensuring the safety of its occupants. That's why we use only the best materials and employ skilled professionals who are trained in the latest roofing practices. Our commitment to excellence is evident in every project we undertake. As a fully licensed and insured roofing company, we prioritize safety and adhere to industry regulations and best practices. We take every precaution to create a safe working environment for our team and minimize any disruptions to your daily routine. When you choose BRVT Roofing, you can trust that you are working with a reliable and reputable company that will deliver exceptional results. We are committed to exceeding your expectations and providing you with a roof that is built to last. Contact us today for all your new construction flat roof installation and repair needs.
Nice to have
• NYC skyline background with commercial roofing pictures of torching roofing

```html
<!DOCTYPE html>
<html lang="en">
<head>
<meta charset="utf-8">
<title>BRVT Roofing</title>
<link href="https://fonts.googleapis.com/css2?family=Cinzel:wght@400;600;700&family=Poppins:wght@400;500;700&display=swap" rel="stylesheet">
<style>
:root{
  --orange:#f26522;
  --orange-light:#ff8a2a;
  --ink:#222;
  --dark:#333;
  --darker:#232323;
  --nav:#3a3a3a;
  --muted:#555;
  --pale:#f4f4f4;
  --beige:#e9e1d3;
  --white:#fff;
}
*{box-sizing:border-box;margin:0;padding:0}
html,body{width:1200px;height:4423px;overflow:hidden}
body{position:relative;font-family:'Poppins',sans-serif;color:var(--ink);background:var(--white)}
.abs{position:absolute}
.serif{font-family:'Cinzel',serif;font-variant:small-caps}
.btn{position:absolute;display:flex;align-items:center;justify-content:center;font-family:'Cinzel',serif;font-weight:600;color:var(--white);letter-spacing:1px}
.btn-orange{background:var(--orange)}
.btn-dark{background:var(--dark)}
.photo{position:absolute}

/* header */
.brand{left:74px;top:30px;font-family:'Cinzel',serif;font-size:28px;color:var(--ink);display:flex;align-items:center;gap:12px}
.brand-mark{width:18px;height:18px;background:var(--orange)}
.header-phone{left:532px;top:31px;display:flex;align-items:center;gap:16px;font-family:'Cinzel',serif;font-size:33px;color:var(--ink)}
.phone-ring{width:52px;height:52px;border:2px solid var(--orange);border-radius:50%;display:flex;align-items:center;justify-content:center}
.quote-btn{left:855px;top:29px;width:271px;height:59px;font-size:21px}
.main-nav{left:0;top:115px;width:1200px;height:69px;background:var(--nav);display:flex;justify-content:center;gap:60px;align-items:center}
.main-nav a{color:var(--white);text-decoration:none;font-family:'Cinzel',serif;font-size:19px;letter-spacing:1px}

/* hero */
.hero{left:0;top:184px;width:1200px;height:635px;background:linear-gradient(90deg,#6c7378 0%,#8a9096 45%,#5a5f64 75%,#3d4044 100%)}
.hero-title{left:74px;top:372px;font-size:60px;color:var(--white);font-weight:700;letter-spacing:2px}
.hero-sub{left:74px;top:447px;width:600px;font-size:24px;line-height:32px;font-weight:700;color:var(--white)}
.hero-btn{left:74px;top:563px;width:168px;height:53px;font-size:20px}
.dots{left:565px;top:771px;display:flex;gap:10px}
.dots span{width:11px;height:11px;border-radius:50%;background:#222}
.dots span:first-child{background:var(--orange)}

/* welcome */
.corner-top{left:60px;top:896px;width:189px;height:143px;background:var(--orange)}
.corner-bottom{left:60px;top:1217px;width:189px;height:143px;background:var(--darker)}
.welcome-photo{left:72px;top:910px;width:515px;height:436px;border-radius:0 34px 34px 34px;background:linear-gradient(160deg,#6f7d88,#3c4a5a 60%,#2d3946)}
.welcome-title{left:615px;top:958px;font-size:50px;line-height:54px;font-weight:600}
.welcome-title em{font-style:normal;color:var(--orange)}
.welcome-text{left:615px;top:1084px;width:510px;font-size:15px;line-height:31px;color:var(--muted)}
.welcome-btn{left:615px;top:1235px;width:166px;height:54px;font-size:17px}

/* services */
.services-band{left:0;top:1451px;width:1200px;height:288px;background:linear-gradient(180deg,#e8571a,var(--orange-light))}
.services-title{left:0;top:1500px;width:1200px;text-align:center;color:var(--white);font-size:56px;font-weight:600}
.service-card{position:absolute;top:1598px;width:330px;height:279px;border:6px solid var(--white);border-radius:18px;box-shadow:0 2px 8px rgba(0,0,0,.25)}
.service-name{position:absolute;top:1903px;width:330px;text-align:center;color:var(--orange);font-size:29px;line-height:33px;font-weight:600}
.service-text{position:absolute;top:1983px;width:330px;text-align:center;font-size:15px;line-height:29px;color:var(--muted)}
.service-btn{top:2093px;width:168px;height:55px;font-size:17px}
.slider-arrow{position:absolute;top:1832px}

/* expert */
.expert-edge{left:0;top:2240px;width:1200px;height:581px;background:var(--beige)}
.expert-photo{left:0;top:2257px;width:1200px;height:547px;background:linear-gradient(90deg,#000 0%,#0a0a0a 30%,#56606a 58%,#7d8891 80%,#6b747c 100%)}
.expert-title{left:74px;top:2322px;font-size:52px;line-height:50px;color:var(--white);font-weight:600}
.expert-sub{left:74px;top:2457px;font-size:36px;color:var(--orange);font-weight:600}
.expert-text{left:74px;top:2512px;width:560px;font-size:15px;line-height:33px;color:var(--white)}
.expert-btn{left:74px;top:2673px;width:168px;height:55px;font-size:17px}

/* gallery */
.gallery-title{left:0;top:2885px;width:1200px;text-align:center;font-size:54px;font-weight:600}
.gallery-btn{left:517px;top:3456px;width:166px;height:55px;font-size:17px}

/* newsletter */
.newsletter{left:0;top:3580px;width:1200px;height:432px;background:var(--pale)}
.news-title{left:0;top:3680px;width:1200px;text-align:center;font-size:42px;line-height:48px;font-weight:600}
.news-sub{left:0;top:3798px;width:1200px;text-align:center;font-size:18px;color:#333}
.email-field{left:290px;top:3851px;width:445px;height:55px;border:2px solid #ccc;background:var(--white);padding-left:14px;display:flex;align-items:center;font-size:13px;color:#444}
.subscribe-btn{left:747px;top:3851px;width:166px;height:55px;font-size:18px}

/* footer */
.site-footer{left:0;top:4012px;width:1200px;height:335px;background:var(--dark)}
.foot-col{position:absolute;top:4078px;color:var(--white)}
.foot-col h4{font-family:'Cinzel',serif;font-variant:small-caps;font-weight:400;font-size:25px;margin-bottom:14px;letter-spacing:1px}
.foot-col li{list-style:none;font-size:15px;line-height:41px}
.contact-line{display:flex;align-items:center;gap:18px}
.socials{display:flex;gap:16px;margin-top:22px}
.socials span{width:22px;height:22px;border-radius:50%;background:var(--white)}
.copyright{left:0;top:4347px;width:1200px;height:76px;background:var(--darker);color:var(--white);font-size:13px;display:flex;align-items:center;justify-content:center}
</style>
</head>
<body>

<header>
  <div class="abs brand"><span class="brand-mark"></span>BRVT Roofing</div>
  <div class="abs header-phone">
    <span class="phone-ring"><svg width="24" height="24" viewBox="0 0 24 24"><path d="M6.6 10.8c1.4 2.8 3.8 5.1 6.6 6.6l2.2-2.2c.3-.3.7-.4 1-.2 1.1.4 2.3.6 3.6.6.6 0 1 .4 1 1V20c0 .6-.4 1-1 1C10.6 21 3 13.4 3 4c0-.6.4-1 1-1h3.5c.6 0 1 .4 1 1 0 1.3.2 2.5.6 3.6.1.3 0 .7-.2 1z" fill="none" stroke="#f26522" stroke-width="1.6"/></svg></span>
    555-014-2290
  </div>
  <div class="btn btn-orange quote-btn">GET A FREE QUOTE</div>
  <nav class="abs main-nav">
    <a href="#">Home</a><a href="#">About</a><a href="#">Services</a><a href="#">Photo Gallery</a><a href="#">Contact</a>
  </nav>
</header>

<section>
  <div class="photo hero" role="img" aria-label="Roofer torching a flat roof above the New York City skyline"></div>
  <h1 class="abs serif hero-title">BRVT Roofing</h1>
  <p class="abs hero-sub">Professional &amp; Affordable Roofing Services. Call Today For a Free Quote! Storm damage, roof installation, roof repair.</p>
  <div class="btn btn-orange hero-btn serif">Book Now</div>
  <div class="abs dots"><span></span><span></span><span></span><span></span></div>
</section>

<section>
  <div class="abs corner-top"></div>
  <div class="abs corner-bottom"></div>
  <div class="photo welcome-photo" role="img" aria-label="Worker torching rolled roofing membrane on a flat roof"></div>
  <h2 class="abs serif welcome-title">Welcome to<br><em>BRVT Roofing</em></h2>
  <p class="abs welcome-text">Marcus brought together the best in the business to create his dream. Though he takes pride in all aspects of roofing, working and living on the coast has lead to a passion for quick, efficient, and transparent repairs to storm damaged homes.</p>
  <div class="btn btn-orange welcome-btn serif">Learn More</div>
</section>

<section>
  <div class="photo services-band" role="img" aria-label="Orange tinted city skyline"></div>
  <h2 class="abs serif services-title">Our Services</h2>

  <svg class="slider-arrow" style="left:24px" width="30" height="48" viewBox="0 0 30 48"><path d="M26 2 4 24l22 22" fill="none" stroke="#555" stroke-width="3"/></svg>
  <svg class="slider-arrow" style="left:1140px" width="30" height="48" viewBox="0 0 30 48"><path d="m4 2 22 22L4 46" fill="none" stroke="#555" stroke-width="3"/></svg>

  <div class="service-card" style="left:74px;background:linear-gradient(160deg,#c7ccd0,#8d9499)" role="img" aria-label="Roofer repairing a roof leak"></div>
  <div class="service-card" style="left:434px;background:linear-gradient(160deg,#d9622c,#a9421c)" role="img" aria-label="Worker cleaning a tiled roof around a skylight"></div>
  <div class="service-card" style="left:795px;background:linear-gradient(160deg,#b8c0c8,#e9ecee)" role="img" aria-label="Worker applying waterproof coating to a roof"></div>

  <h3 class="service-name serif" style="left:74px">Roof Leak<br>Repairs</h3>
  <h3 class="service-name serif" style="left:434px">Flashing<br>Services</h3>
  <h3 class="service-name serif" style="left:795px">Waterproofing<br>Experts</h3>

  <p class="service-text" style="left:74px">Sed ut perspiciatis unde omnis iste natus error sit voluptatem accusantium doloremque laudantium.</p>
  <p class="service-text" style="left:434px">Sed ut perspiciatis unde omnis iste natus error sit voluptatem accusantium doloremque laudantium.</p>
  <p class="service-text" style="left:795px">Sed ut perspiciatis unde omnis iste natus error sit voluptatem accusantium doloremque laudantium.</p>

  <div class="btn btn-dark service-btn serif" style="left:155px">Learn More</div>
  <div class="btn btn-dark service-btn serif" style="left:516px">Learn More</div>
  <div class="btn btn-dark service-btn serif" style="left:877px">Learn More</div>
</section>

<section>
  <div class="abs expert-edge"></div>
  <div class="photo expert-photo" role="img" aria-label="Close view of a torch sealing a roll of flat roof membrane"></div>
  <h2 class="abs serif expert-title">Expert Flat Roof<br>Services</h2>
  <h3 class="abs serif expert-sub">Perfect Installs</h3>
  <p class="abs expert-text">Your roof is your main defense against the elements. Let us walk you through the best options to fit your needs and once you feel comfortable with your choice, we'll handle the complete installation.</p>
  <div class="btn btn-orange expert-btn serif">Learn More</div>
  <svg class="abs" style="left:263px;top:2686px" width="22" height="32" viewBox="0 0 22 32"><path d="M19 2 4 16l15 14" fill="none" stroke="#fff" stroke-width="3"/></svg>
  <svg class="abs" style="left:308px;top:2686px" width="22" height="32" viewBox="0 0 22 32"><path d="m3 2 15 14L3 30" fill="none" stroke="#fff" stroke-width="3"/></svg>
</section>

<section>
  <h2 class="abs serif gallery-title">Photo Gallery</h2>
  <div class="photo" style="left:74px;top:2982px;width:340px;height:204px;background:linear-gradient(160deg,#6f7d88,#2f3b47)" role="img" aria-label="Roofer torching membrane"></div>
  <div class="photo" style="left:431px;top:2982px;width:340px;height:204px;background:linear-gradient(160deg,#7a7470,#c08a3a)" role="img" aria-label="Nail gun on roof shingles"></div>
  <div class="photo" style="left:788px;top:2982px;width:340px;height:204px;background:linear-gradient(160deg,#4e5358,#d6dadd)" role="img" aria-label="Worker spreading white roof coating"></div>
  <div class="photo" style="left:74px;top:3205px;width:340px;height:205px;background:linear-gradient(180deg,#a9cbe8,#5d7f9e)" role="img" aria-label="Metal roof under a blue sky"></div>
  <div class="photo" style="left:431px;top:3205px;width:340px;height:205px;background:linear-gradient(160deg,#3e6a55,#9aa3a7)" role="img" aria-label="Roofer in work trousers with torch"></div>
  <div class="photo" style="left:788px;top:3205px;width:340px;height:205px;background:linear-gradient(160deg,#3a3c40,#8a6248)" role="img" aria-label="Rooftop terrace with outdoor furniture"></div>
  <div class="btn btn-dark gallery-btn serif">View All</div>
</section>

<section>
  <div class="abs newsletter"></div>
  <h2 class="abs serif news-title">Flat roof installation roof repair storm<br>damage insurance specialists</h2>
  <p class="abs news-sub">Sign up to receive maintenance reminders and hear about our latest projects.</p>
  <div class="abs email-field">Email Address</div>
  <div class="btn btn-orange subscribe-btn">SUBSCRIBE</div>
</section>

<footer>
  <div class="abs site-footer"></div>
  <div class="foot-col" style="left:76px"><h4>Site Map</h4><ul><li>Home</li><li>About</li><li>Services</li><li>Photo Gallery</li><li>Contact</li></ul></div>
  <div class="foot-col" style="left:316px"><h4>Services</h4><ul><li>Perfect Installs</li><li>Reliable Upgrades</li><li>Upkeep &amp; Repair</li></ul></div>
  <div class="foot-col" style="left:579px"><h4>Hours</h4><ul><li>Monday - Friday: 8am - 5pm</li><li>Saturday - Sunday: 8am-12</li></ul></div>
  <div class="foot-col" style="left:883px"><h4>Contact Us</h4><ul>
    <li class="contact-line"><svg width="14" height="14" viewBox="0 0 24 24"><path d="M6.6 10.8c1.4 2.8 3.8 5.1 6.6 6.6l2.2-2.2c.3-.3.7-.4 1-.2 1.1.4 2.3.6 3.6.6.6 0 1 .4 1 1V20c0 .6-.4 1-1 1C10.6 21 3 13.4 3 4c0-.6.4-1 1-1h3.5c.6 0 1 .4 1 1 0 1.3.2 2.5.6 3.6.1.3 0 .7-.2 1z" fill="#f26522"/></svg>555-014-2290</li>
    <li class="contact-line"><svg width="14" height="12" viewBox="0 0 14 12"><rect width="14" height="12" fill="#f26522"/><path d="m0 1 7 5 7-5" fill="none" stroke="#333" stroke-width="1.4"/></svg>info@brvtroofing.example</li>
  </ul>
  <div class="socials"><span></span><span></span><span></span><span></span><span></span></div>
  </div>
  <div class="abs copyright">Copyright ©2024 BRVT Roofing. All Rights Reserved.</div>
</footer>

</body>
</html>
```